Varnik Holdings — Business Card Design Brief
Overview
Design a double-sided business card for Varnik Holdings that highlights our two service arms: Varnik Communications (telecommunications) and Varnik Energy (business energy solutions). The card should feel smart and stand out when handed to clients.

Objectives
Showcase our areas of specialty clearly.
Reflect the overall Varnik / Varnik Holdings brand while acknowledging both arms.
Explore using both logos (Communications + Energy) or one unified logo, depending on the design.

Deliverables
One double-sided business card design (front + back).

Content & Copy
Front (preferred): Logo: Varnik / Varnik Holdings
Descriptor: Business Communications | Business Energy
Back:My contact details and company details
Core products: Business Mobile • Telephony • Internet • Business Energy Solutions

Brand & Visual Direction
We have a group logo currently tailored more toward telecoms, plus a separate Varnik Energy logo.
Please explore layouts that use both logos or just one, whichever works best.
Color: I wouldn't mind seeing an option using our the Blue/Purple gradient from our website (varnik-example.co.uk), but also open to non-gradient approaches and other colours..

Overall look: Smart, modern, and distinctive.
Format & Print Specs
Double-sided business card format. (Use a standard size

Must-Haves
Front: Varnik wording or Varnik Holdings wording with atleast 1 logo also on front “Business Communications | Business Energy.”

Back: Contact + company details and core products.
A design that stands out while remaining professional.

Nice-to-Have Options
A gradient version using our site’s Blue/Purple gradient.
A non-gradient version.
A dual-logo treatment versus a single-logo treatment.

Thanks
Owen

```html
<!DOCTYPE html>
<html lang="en">
<head>
<meta charset="utf-8">
<title>Varnik Holdings — Business Card</title>
<link rel="stylesheet" href="https://fonts.googleapis.com/css2?family=Montserrat:wght@700;800&family=Arimo:wght@400;700&display=swap">
<style>
  :root {
    --backdrop: #e4e4e4;
    --card-light: #ffffff;
    --card-dark: #333333;
    --navy: #1c1a6a;
    --sky: #1e8ad8;
    --ink: #3a3a3a;
    --green: #5cb82a;
    --lime: #8cc63f;
    --blue: #1a64d6;
    --white: #ffffff;
  }
  * { margin: 0; padding: 0; box-sizing: border-box; }
  html, body { width: 1200px; height: 1200px; overflow: hidden; background: var(--backdrop); }
  body { position: relative; font-family: "Arimo", Arial, sans-serif; }

  .card { position: absolute; left: 256px; width: 688px; height: 394px; }
  .card-front { top: 160px; background: var(--card-light); }
  .card-back { top: 650px; background: var(--card-dark); }

  .wordmark { font-family: "Montserrat", Arial, sans-serif; font-weight: 800; letter-spacing: -0.5px; line-height: 1; }
  .front-wordmark { position: absolute; left: 44px; top: 46px; font-size: 60px; color: var(--navy); }

  .person-name { position: absolute; left: 45px; top: 134px; font-family: "Montserrat", Arial, sans-serif; font-weight: 700; font-size: 25px; color: var(--navy); }
  .person-title { position: absolute; left: 45px; top: 163px; font-size: 15px; color: var(--sky); }

  .address { position: absolute; left: 45px; top: 195px; font-size: 16.5px; line-height: 21px; color: var(--ink); }

  .contact-list { position: absolute; left: 45px; top: 249px; list-style: none; font-size: 16.5px; color: var(--ink); }
  .contact-list li { display: flex; align-items: center; height: 20.5px; }
  .contact-list svg { width: 14px; height: 14px; margin-right: 12px; fill: var(--navy); }

  .products { position: absolute; left: 47px; top: 353px; font-size: 17.5px; color: #222; white-space: nowrap; }
  .products .dot { color: var(--green); margin: 0 6px; }

  .arm { position: absolute; left: 372px; display: flex; align-items: center; gap: 16px; }
  .arm-energy { top: 62px; }
  .arm-comms { top: 222px; }
  .arm-mark { width: 92px; height: 92px; border-radius: 50%; border: 9px solid var(--green); }
  .arm-comms .arm-mark { border-color: var(--blue); }
  .arm-name { font-family: "Arimo", Arial, sans-serif; font-weight: 700; font-size: 21px; color: var(--green); }
  .arm-comms .arm-name { color: var(--blue); }

  .divider { position: absolute; left: 355px; top: 96px; width: 1.5px; height: 214px; background: #d8d8d8; }
  .back-half { position: absolute; top: 90px; width: 300px; text-align: center; }
  .back-left { left: 55px; }
  .back-right { left: 344px; }
  .back-mark { width: 110px; height: 110px; margin: 0 auto 18px; border-radius: 50%; border: 11px solid var(--green); }
  .back-right .back-mark { border-color: var(--blue); }
  .back-wordmark { font-size: 54px; color: var(--white); }
  .back-tag { margin-top: 10px; font-size: 16.5px; }
  .back-left .back-tag { color: #2a7de1; }
  .back-right .back-tag { color: var(--lime); letter-spacing: 3px; }
</style>
</head>
<body>
  <section class="card card-front">
    <div class="wordmark front-wordmark">Varnik</div>
    <div class="person-name">DANIEL HART</div>
    <div class="person-title">President</div>
    <p class="address">412 Alder Crescent<br>Kelso, Canada 50218</p>
    <ul class="contact-list">
      <li><svg viewBox="0 0 24 24"><path d="M6.6 10.8a15.1 15.1 0 0 0 6.6 6.6l2.2-2.2c.3-.3.7-.4 1-.2 1.1.4 2.3.6 3.6.6.6 0 1 .4 1 1V20c0 .6-.4 1-1 1A17 17 0 0 1 3 4c0-.6.4-1 1-1h3.5c.6 0 1 .4 1 1 0 1.3.2 2.5.6 3.6.1.3 0 .7-.2 1z"/></svg>555-014-2287</li>
      <li><svg viewBox="0 0 24 24"><path d="M7 1h10a2 2 0 0 1 2 2v18a2 2 0 0 1-2 2H7a2 2 0 0 1-2-2V3a2 2 0 0 1 2-2zm0 3v15h10V4z"/></svg>555-019-6631</li>
      <li><svg viewBox="0 0 24 24"><path d="M2 5h20v14H2zm2 2v.5l8 5 8-5V7zm0 3v7h16v-7l-8 5z"/></svg>info@varnik-example.co.uk</li>
      <li><svg viewBox="0 0 24 24"><path d="M12 2a10 10 0 1 0 0 20 10 10 0 0 0 0-20zm0 2c1 0 2.2 1.8 2.7 5H9.3C9.8 5.8 11 4 12 4zM4.3 11h3c0 .7 0 1.4.1 2h-3a8 8 0 0 1 0-2zm5 0h5.4a14 14 0 0 1 0 2H9.3a14 14 0 0 1 0-2zm7.4 0h3a8 8 0 0 1 0 2h-3c.1-.6.1-1.3 0-2zM12 20c-1 0-2.2-1.8-2.7-5h5.4c-.5 3.2-1.7 5-2.7 5z"/></svg>www.varnik-example.co.uk</li>
    </ul>

    <div class="arm arm-energy">
      <div class="arm-mark"></div>
      <span class="arm-name">Varnik Energy</span>
    </div>
    <div class="arm arm-comms">
      <div class="arm-mark"></div>
      <span class="arm-name">Varnik Communications</span>
    </div>

    <p class="products">Business Mobile<span class="dot">•</span>Telephony<span class="dot">•</span>Internet<span class="dot">•</span>Business Energy Solutions</p>
  </section>

  <section class="card card-back">
    <div class="back-half back-left">
      <div class="back-mark"></div>
      <div class="wordmark back-wordmark">Varnik</div>
      <div class="back-tag">BUSINESS COMMUNICATIONS</div>
    </div>
    <div class="divider"></div>
    <div class="back-half back-right">
      <div class="back-mark"></div>
      <div class="wordmark back-wordmark">Varnik</div>
      <div class="back-tag">BUSINESS ENERGY</div>
    </div>
  </section>
</body>
</html>
```